Pellowar

We need logo and wesbsite for a software development company based out of Hyderabad, India focused on startups and mid sized companies focused on build a new software products in USA and Europe countires.

Target Market(s)

startup and midsized companies in teh USA and Europe for software product development.

Industry/Entity Type

software development

Coding

Coded - Design and coding required

Number of Pages Required

5+ page

Requirements
Must have
• latest design concepts and very elegant
Nice to have
• each page should have images that reflects the content
Should not have
• too many colors

```html
<!DOCTYPE html>
<html lang="en">
<head>
<meta charset="utf-8">
<title>Pellowar — Software Development</title>
<link href="https://fonts.googleapis.com/css2?family=Montserrat:wght@400;500;600;700;800&family=Open+Sans:wght@400;600&display=swap" rel="stylesheet">
<style>
:root{
  --navy:#0f2a4f;
  --navy-deep:#0b2142;
  --red:#d71a2b;
  --ink:#1b1f2a;
  --muted:#6b7280;
  --line:#e3e6ec;
  --paper:#ffffff;
  --soft:#f4f6f9;
}
*{box-sizing:border-box;margin:0;padding:0}
html,body{width:1200px;height:4284px;overflow:hidden}
body{font-family:"Open Sans",Arial,sans-serif;color:var(--ink);background:var(--paper);position:relative}
h1,h2,h3,h4,.nav,.btn,.label{font-family:"Montserrat",Arial,sans-serif}
.abs{position:absolute}

/* nav */
.topbar{position:absolute;left:0;top:0;width:1200px;height:72px;background:#fff;display:flex;align-items:center;padding:0 110px;box-shadow:0 2px 8px rgba(0,0,0,.06);z-index:2}
.nav{display:flex;gap:30px;font-size:12px;font-weight:700;color:var(--ink)}
.nav a{color:inherit;text-decoration:none}
.nav a.active{color:var(--red);border-bottom:2px solid var(--red);padding-bottom:4px}
.brand{position:absolute;left:520px;top:14px;text-align:center;width:170px}
.brand .name{font-family:"Montserrat",sans-serif;font-weight:800;font-size:22px;color:var(--navy);letter-spacing:.5px}
.brand .sub{font-family:"Montserrat",sans-serif;font-weight:700;font-size:9px;color:var(--red);letter-spacing:1px}
.nav-right{position:absolute;right:110px;top:0;height:72px;display:flex;align-items:center;gap:30px}
.btn{display:inline-block;font-size:12px;font-weight:700;color:#fff;padding:12px 20px;text-decoration:none;letter-spacing:.5px}
.btn-red{background:var(--red)}
.btn-navy{background:var(--navy)}

/* hero */
.hero{position:absolute;left:0;top:72px;width:1200px;height:648px;background:linear-gradient(90deg,#2a2a2e 0%,#3d3b3c 40%,#8d8279 70%,#c9c0b6 100%)}
.hero .photo{position:absolute;inset:0;background:radial-gradient(circle at 76% 40%,rgba(160,120,95,.55),transparent 35%)}
.hero-copy{position:absolute;left:110px;top:200px;width:520px;color:#fff}
.hero-copy .label{font-size:11px;font-weight:600;letter-spacing:1px;margin-bottom:14px}
.hero-copy h1{font-size:40px;line-height:46px;font-weight:800;text-transform:uppercase}
.hero-copy p{font-size:12px;line-height:19px;margin:20px 0 30px;color:#e8e8e8;width:420px}
.hero-copy .btn{margin-right:12px}
.social{position:absolute;right:28px;top:250px;display:flex;flex-direction:column;gap:14px}
.social span{width:14px;height:14px;border-radius:50%;border:1.5px solid #fff;display:block}
.scroll{position:absolute;left:584px;top:724px;width:32px;height:32px;border-radius:50%;background:#fff;border:1px solid var(--line);display:flex;align-items:center;justify-content:center}

/* section labels */
.label.tag{display:flex;align-items:center;gap:8px;font-size:12px;font-weight:700;color:var(--navy);letter-spacing:1px}
.tag::before{content:"";width:14px;height:3px;background:var(--red)}
.tag.light{color:#fff}
.tag.center{justify-content:center}

/* about */
.about-head{left:110px;top:820px;width:440px}
.about-head h2{font-size:30px;line-height:38px;font-weight:500;color:var(--navy);margin-top:14px}
.about-head h2 b{font-weight:800}
.about-text{left:640px;top:820px;width:450px;font-size:12px;line-height:19px;color:var(--muted)}
.more{display:inline-flex;align-items:center;gap:8px;font-family:"Montserrat",sans-serif;font-size:11px;font-weight:700;color:var(--navy);margin-top:18px}
.more::before{content:"";width:26px;height:26px;border:1.5px solid var(--navy);border-radius:50%}
.frame{border:3px solid var(--red)}
.about-frame{left:130px;top:1024px;width:680px;height:340px}
.about-photo{left:150px;top:1044px;width:660px;height:380px;background:linear-gradient(135deg,#c9ccd2,#7c8592 55%,#3f4a5a)}
.about-small1{left:760px;top:1160px;width:180px;height:130px;background:linear-gradient(135deg,#d9c8b8,#8a7a70);border:6px solid #fff;box-shadow:0 6px 20px rgba(0,0,0,.15)}
.about-small2{left:880px;top:1260px;width:210px;height:150px;background:linear-gradient(135deg,#b8c3cf,#56657a);border:6px solid #fff;box-shadow:0 6px 20px rgba(0,0,0,.15)}
.about-caption{left:150px;top:1448px;width:420px;font-size:11px;line-height:17px;color:var(--muted)}

/* product */
.product{position:absolute;left:0;top:1640px;width:1200px;height:520px;background:var(--navy);color:#fff;text-align:center}
.product h2{font-size:30px;font-weight:800;margin-top:12px}
.product p.lead{width:800px;margin:24px auto 0;font-size:13px;line-height:20px;font-weight:600}
.cards{position:absolute;left:90px;top:250px;width:1020px;display:flex;gap:4px}
.card{flex:1;height:168px;background:#fff;color:var(--ink);display:flex;flex-direction:column;align-items:center;justify-content:center;gap:22px;font-family:"Montserrat",sans-serif;font-weight:700;font-size:14px;box-shadow:0 8px 20px rgba(0,0,0,.2)}
.arrow{position:absolute;top:326px;color:#fff;font-size:26px;font-family:"Montserrat",sans-serif}

/* process */
.process-head{left:0;top:2196px;width:1200px;text-align:center}
.process-head h2{font-size:30px;font-weight:800;color:var(--navy);margin-top:12px}
.steps{left:110px;top:2380px;width:980px;display:flex}
.step{flex:1;text-align:center;position:relative}
.step .dot{width:84px;height:84px;border-radius:50%;margin:0 auto;display:flex;align-items:center;justify-content:center;background:var(--navy)}
.step.red .dot{background:var(--red)}
.step .no{font-family:"Montserrat",sans-serif;font-size:14px;color:var(--muted);letter-spacing:1px;margin-top:20px}
.step h4{font-size:15px;font-weight:700;margin-top:8px}
.step p{font-size:11px;line-height:17px;color:var(--muted);width:250px;margin:10px auto 0}
.steps-line{left:276px;top:2422px;width:648px;height:0;border-top:2px dashed var(--line)}

/* case study */
.case-copy{left:110px;top:2810px;width:450px}
.case-copy h2{font-size:40px;font-weight:800;color:var(--navy);margin:14px 0 22px}
.case-copy p{font-size:12px;line-height:19px;color:var(--muted);margin-bottom:14px}
.case-frame{left:710px;top:2800px;width:430px;height:460px;border:3px solid var(--navy)}
.case-photo{left:660px;top:2830px;width:500px;height:400px;background:linear-gradient(135deg,#dde2e8,#9aa4b1 50%,#4f5b6d)}

/* team */
.team{position:absolute;left:0;top:3340px;width:1200px;height:580px;background:var(--soft)}
.team-photo{left:120px;top:3420px;width:400px;height:420px;background:linear-gradient(135deg,#56515a,#2f3040 60%,#1c1d26)}
.team-frame{left:100px;top:3400px;width:360px;height:460px}
.team-copy{left:650px;top:3460px;width:450px}
.team-copy h2{font-size:30px;font-weight:800;color:var(--navy);margin:12px 0 22px}
.team-copy p{font-size:12px;line-height:19px;color:var(--muted);margin-bottom:14px}

/* footer */
.footer{position:absolute;left:0;top:3920px;width:1200px;height:364px;background:var(--navy-deep);color:#cfd6e2}
.fcols{position:absolute;left:110px;top:60px;width:980px;display:flex;gap:40px}
.fcol h4{font-size:13px;font-weight:700;color:#fff;margin-bottom:18px}
.fcol p,.fcol li{font-size:11px;line-height:22px;list-style:none}
.fcol li::before{content:"› ";color:var(--red)}
.fcol .ci{display:flex;gap:10px;align-items:flex-start;margin-bottom:10px}
.fcol .ci b{color:#fff}
.copy{position:absolute;left:0;bottom:0;width:1200px;height:50px;border-top:1px solid rgba(255,255,255,.12);text-align:center;line-height:50px;font-size:11px;color:#aeb7c6}
</style>
</head>
<body>

<header class="topbar">
  <nav class="nav">
    <a class="active">HOME</a><a>ABOUT</a><a>BUILD YOUR PRODUCT</a><a>CASE STUDY</a>
  </nav>
  <div class="brand"><div class="name">PELLOWAR</div><div class="sub">SOFTWARE DEVELOPMENT</div></div>
  <div class="nav-right nav"><a>BUILD YOUR TEAM</a><a>CONTACT</a><a class="btn btn-red">GET STARTED</a></div>
</header>

<section class="hero">
  <div class="photo" role="img" aria-label="Photo of a smiling developer working at a laptop in a bright office"></div>
  <div class="hero-copy">
    <div class="label">WELCOME TO PELLOWAR</div>
    <h1>We are a software development company based out of Hyderabad</h1>
    <p>We build and scale digital products for startups and growing companies, from early ideas to launch and beyond, with teams you can trust.</p>
    <a class="btn btn-red">GET STARTED</a><a class="btn btn-navy">LEARN MORE</a>
  </div>
  <div class="social"><span></span><span></span><span></span><span></span></div>
</section>
<div class="scroll"><svg width="12" height="12" viewBox="0 0 12 12"><path d="M6 2v8M2 6l4 4 4-4" stroke="#0f2a4f" stroke-width="1.6" fill="none"/></svg></div>

<div class="abs about-head">
  <div class="label tag">ABOUT US</div>
  <h2>Focused on building <b>new software products in USA and Europe</b> countries</h2>
</div>
<div class="abs about-text">
  We are a group of entrepreneurs, technocrats, software architects, and delivery heads who have come together to serve startups, product companies, and enterprises with their product development. We are proud to understand your product and help design, build, maintain and operate your product. Pellowar quickly set up a team of UX experts, business analysts, developers and QA engineers.
  <div class="more">LEARN MORE ABOUT US</div>
</div>
<div class="abs frame about-frame"></div>
<div class="abs about-photo" role="img" aria-label="Photo of a development team collaborating at desks with computers"></div>
<div class="abs about-small1" role="img" aria-label="Photo of colleagues talking in a meeting"></div>
<div class="abs about-small2" role="img" aria-label="Photo of a team working together on laptops"></div>
<p class="abs about-caption">Building software products is complex and changing day by day. The right partner is very important, bringing experience, developing software capacity and a team of expertise that can start quickly.</p>

<section class="product">
  <div style="padding-top:58px" class="label tag light center">PRODUCT</div>
  <h2>Build Your Product</h2>
  <p class="lead">Startup owners must use the CEO mindset while building a software product. Think of the bigger picture. Focus on the outcome and set aside the tiny technical details. Focus on human resources and Process.</p>
  <span class="arrow" style="left:40px">‹</span><span class="arrow" style="right:40px">›</span>
  <div class="cards">
    <div class="card"><svg width="48" height="48" viewBox="0 0 48 48"><circle cx="24" cy="14" r="8" fill="#0f2a4f"/><path d="M8 44c0-10 7-16 16-16s16 6 16 16z" fill="#d71a2b"/></svg>Project Manager</div>
    <div class="card"><svg width="48" height="48" viewBox="0 0 48 48"><circle cx="24" cy="10" r="6" fill="#d71a2b"/><circle cx="10" cy="32" r="5" fill="#0f2a4f"/><circle cx="38" cy="32" r="5" fill="#0f2a4f"/><path d="M24 16v8M10 27v-3h28v3" stroke="#0f2a4f" stroke-width="2" fill="none"/></svg>Team Lead</div>
    <div class="card"><svg width="48" height="48" viewBox="0 0 48 48"><path d="M4 22l10-8 10 6 10-6 10 8-10 12-10-6-10 6z" fill="#0f2a4f"/><path d="M18 26l6 4 6-4" stroke="#d71a2b" stroke-width="3" fill="none"/></svg>Business analyst</div>
    <div class="card"><svg width="48" height="48" viewBox="0 0 48 48"><rect x="6" y="8" width="36" height="28" rx="2" fill="#0f2a4f"/><path d="M18 16l-6 6 6 6M30 16l6 6-6 6" stroke="#d71a2b" stroke-width="2.5" fill="none"/><rect x="16" y="38" width="16" height="3" fill="#0f2a4f"/></svg>Developers</div>
    <div class="card"><svg width="48" height="48" viewBox="0 0 48 48"><circle cx="22" cy="14" r="8" fill="#0f2a4f"/><path d="M6 44c0-10 7-16 16-16" fill="#0f2a4f"/><path d="M6 44c0-10 7-16 16-16v16z" fill="#0f2a4f"/><circle cx="34" cy="34" r="9" fill="#d71a2b"/><path d="M30 34l3 3 5-6" stroke="#fff" stroke-width="2" fill="none"/></svg>Testers</div>
  </div>
</section>

<div class="abs process-head">
  <div class="label tag center">STEPS</div>
  <h2>Our Process</h2>
</div>
<div class="abs steps-line"></div>
<div class="abs steps">
  <div class="step"><div class="dot"><svg width="34" height="34" viewBox="0 0 34 34"><rect x="7" y="5" width="20" height="24" rx="2" fill="none" stroke="#fff" stroke-width="2"/><path d="M11 12h12M11 17h12M11 22h8" stroke="#fff" stroke-width="2"/></svg></div><div class="no">STEP - 01</div><h4>Pass cognitive aptitude test</h4><p>Accepting job applications from the entire world means every role on Pellowar involves thousands of applications.</p></div>
  <div class="step red"><div class="dot"><svg width="34" height="34" viewBox="0 0 34 34"><path d="M5 7h24v16H14l-6 5v-5H5z" fill="none" stroke="#fff" stroke-width="2"/></svg></div><div class="no">STEP - 02</div><h4>Pass English proficiency test</h4><p>Someday, technological advancements will make it possible for teams to collaborate without sharing a common language.</p></div>
  <div class="step"><div class="dot"><svg width="34" height="34" viewBox="0 0 34 34"><path d="M12 10l-7 7 7 7M22 10l7 7-7 7" stroke="#fff" stroke-width="2.5" fill="none"/></svg></div><div class="no">STEP - 03</div><h4>Prove real-world job skills</h4><p>Of course, there's much more to being a great developer than intelligence and language skills. The next step is to complete a real task.</p></div>
</div>

<div class="abs case-copy">
  <div class="label tag">RESOURCES</div>
  <h2>Case Study</h2>
  <p>Many business owners have great ideas but no experience with the actual product. Once you have an idea in mind, you will require software development aid at some point — whether your concept is for next-generation software or an invention approach to offering an existing service. It might also be the development of a mobile app or web-based software. Whatever product you're working on, you'll need a technical co-founder to help you get it off the ground.</p>
  <p>An MVP is a simple, functional version of your product that can be produced quickly and cheaply.</p>
  <div class="more">LEARN MORE ABOUT US</div>
</div>
<div class="abs case-frame"></div>
<div class="abs case-photo" role="img" aria-label="Photo of a team reviewing work together at a bright office desk"></div>

<section class="team"></section>
<div class="abs frame team-frame"></div>
<div class="abs team-photo" role="img" aria-label="Photo of developers working at screens in a dark office"></div>
<div class="abs team-copy">
  <div class="label tag">WHY CHOOSE US</div>
  <h2>Build Your Team</h2>
  <p>Break free from traditional recruiting with us. At Pellowar, we help you achieve the right organizational metric with resources who can take your business to the next level.</p>
  <p>We have spent years trying to innovate and improve the process of hiring talented individuals who can take businesses to the next level. We ensure that the workforce we employ for your organization is highly productive and takes you to the golden standards of heights.</p>
  <div class="more">LEARN MORE ABOUT US</div>
</div>

<footer class="footer">
  <div class="fcols">
    <div class="fcol" style="width:300px"><h4>ABOUT US</h4><p>We help founders and growing firms plan, design, build and run software products with dedicated teams and clear, honest delivery every step of the way.</p></div>
    <div class="fcol" style="width:150px"><h4>QUICK LINKS</h4><ul><li>Home</li><li>About Us</li><li>Our Services</li><li>Case Study</li><li>Build Your Team</li></ul></div>
    <div class="fcol" style="width:150px"><h4>OTHER LINKS</h4><ul><li>Terms Of Use</li><li>Privacy Policy</li><li>Help Service</li><li>Contact Us</li><li>FAQ</li></ul></div>
    <div class="fcol" style="width:220px"><h4>CONTACT US</h4>
      <div class="ci"><svg width="14" height="16" viewBox="0 0 14 16"><path d="M7 1a5 5 0 0 1 5 5c0 4-5 9-5 9S2 10 2 6a5 5 0 0 1 5-5z" fill="#d71a2b"/><circle cx="7" cy="6" r="2" fill="#0b2142"/></svg><p>23, Lorem Ipsum Road<br>Hyderabad</p></div>
      <div class="ci"><svg width="14" height="14" viewBox="0 0 14 14"><rect x="1" y="3" width="12" height="8" fill="none" stroke="#d71a2b" stroke-width="1.5"/><path d="M1 3l6 5 6-5" stroke="#d71a2b" stroke-width="1.5" fill="none"/></svg><p>info@pellowar.example</p></div>
      <div class="ci"><svg width="14" height="14" viewBox="0 0 14 14"><path d="M3 1l3 3-2 2c1 2 2 3 4 4l2-2 3 3-2 2C6 13 1 8 1 3z" fill="#d71a2b"/></svg><p><b>+1 555 010 2040</b></p></div>
    </div>
  </div>
  <div class="copy">© 2021 Pellowar. All Rights Reserved</div>
</footer>

</body>
</html>
```